Podcast Cover Art for rebranded podcast - I have inspiration for the designs

I've had a podcast ("Paperboat Radio Hour") since 2018, but I'm in the process of rebranding it. I've attached the old cover art below, which I loved, but I don't need it to look like that at all. The rebranded podcast is called 'Open Window with Marnie Cole.' I've included the show description at the bottom. I've been working on various design options in Canva, but not obsessed with anything yet, but I'm attaching the ones I do like that I think just need some refining. My very favorite is the one labeled 'favorite_Open Window' so I wouldn't mind keeping that general idea but perfected by a designer. Ultimately, I want something cool, fairly clean, modern, eye catching. I'm into neutrals with maybe a pop of color, so think black, white, grey..maybe silver, and I love a pop of red..and I'm not opposed to other options for the pop color. The show is going to be inspiring, entertaining, and funny. Oh and one other idea I had but I'm not sure if it makes sense with the title and/or what the show is about..but a vinyl record with Open Window with Marnie Cole on it somehow, on a record player..not sure.

Ever wonder what it means to truly live authentically? Curious about how to embrace the unpredictability of life? Ready for some heartfelt and lighthearted conversations that inspire and entertain?
Join Marnie Cole as she dives into the raw, real, and unscripted moments of life. In each episode, Marnie brings candid conversations and genuine insights into the ups and downs we all experience. From personal growth and self-discovery to inspiring stories and valuable life lessons, "Open Window" is a space where authenticity reigns and spontaneity is celebrated.
Whether she's sharing her own journey or chatting with inspiring guests, Marnie invites you to explore the beauty of living life without a script. Expect honest reflections, thought-provoking discussions, and a refreshing perspective on navigating life's unpredictable path—all with a dash of fun and humor to keep things lively and entertaining. Step into the unscripted moments of life and tune in for a blend of depth and lightheartedness that will leave you inspired, smiling, and most importantly laughing.

Target Market(s)

25-50 year old women and men (primarily women)

Font styles to use
Sans Serif

Requirements
Should not have
• nothing too feminine or girly, nothing cheesy :)

```html
<!DOCTYPE html>
<html lang="en">
<head>
<meta charset="utf-8">
<title>Open Window with Marnie Cole — Podcast Cover</title>
<link href="https://fonts.googleapis.com/css2?family=Archivo+Black&family=Oswald:wght@500;600;700&family=Josefin+Sans:wght@600&display=swap" rel="stylesheet">
<style>
  :root {
    --charcoal-deep: #141416;
    --charcoal-mid: #2a2a2e;
    --charcoal-glow: #4a4a50;
    --white: #ffffff;
    --silver: #b9b9c0;
    --red: #e5322d;
    --red-edge: #141416;
    --photo-light: #5d5d64;
    --photo-dark: #1c1c1f;
  }
  html, body {
    margin: 0;
    width: 1200px;
    height: 1200px;
    overflow: hidden;
    background: var(--charcoal-deep);
  }
  .cover {
    position: relative;
    width: 1200px;
    height: 1200px;
    overflow: hidden;
    background:
      radial-gradient(circle at 48% 60%, var(--charcoal-glow) 0%, var(--charcoal-mid) 38%, var(--charcoal-deep) 85%);
  }
  .backdrop-photo {
    position: absolute;
    left: 380px;
    top: 600px;
    width: 460px;
    height: 480px;
    border-radius: 50%;
    background: radial-gradient(circle, rgba(150, 150, 160, 0.28) 0%, rgba(60, 60, 66, 0) 70%);
  }
  .host-photo {
    position: absolute;
    left: 730px;
    top: 0;
    width: 470px;
    height: 1200px;
    background: linear-gradient(180deg, var(--photo-light) 0%, #3b3b40 45%, var(--photo-dark) 100%);
  }
  .title-word {
    position: absolute;
    left: 0;
    top: 0;
  }
  .title-word text {
    font-family: "Archivo Black", sans-serif;
    fill: var(--white);
  }
  .line {
    position: absolute;
    margin: 0;
    line-height: 1;
    white-space: nowrap;
    font-family: "Oswald", sans-serif;
  }
  .subtitle {
    left: 150px;
    top: 462px;
    font-weight: 700;
    font-size: 150px;
    letter-spacing: 4px;
    color: var(--red);
    -webkit-text-stroke: 10px var(--red-edge);
    paint-order: stroke fill;
  }
  .with-label {
    left: 88px;
    top: 694px;
    font-weight: 500;
    font-size: 80px;
    letter-spacing: -1px;
    color: var(--silver);
  }
  .host-first {
    left: 162px;
    top: 770px;
    font-weight: 600;
    font-size: 116px;
    letter-spacing: 3px;
    color: var(--white);
  }
  .host-last {
    left: 380px;
    top: 900px;
    font-weight: 600;
    font-size: 100px;
    letter-spacing: 3px;
    color: var(--red);
  }
  .format-label {
    left: 80px;
    top: 1050px;
    font-family: "Josefin Sans", sans-serif;
    font-weight: 600;
    font-size: 30px;
    letter-spacing: 4px;
    color: var(--white);
  }
</style>
</head>
<body>
  <main class="cover">
    <div class="backdrop-photo" role="img" aria-label="Faded photo of a microphone and laptop on a desk"></div>
    <div class="host-photo" role="img" aria-label="Photo of the host with arms raised, smiling, long dark hair"></div>

    <svg class="title-word" width="1200" height="600" viewBox="0 0 1200 600" aria-label="OPEN">
      <text x="84" y="504" font-size="520" textLength="991" lengthAdjust="spacingAndGlyphs">OPEN</text>
    </svg>

    <h1 class="line subtitle">WINDOW</h1>

    <p class="line with-label">WITH</p>
    <p class="line host-first">MARNIE</p>
    <p class="line host-last">COLE</p>

    <p class="line format-label">PODCAST</p>
  </main>
</body>
</html>
```